Modern, clean business card for Clearbrook Optics

Updated business card with a modern look.

Logo on the front
Dr Tavin R Marquell and Associates on the front.
Three locations on the back:
Ridgefront Brantmart
509-555-0142
18342 E Fernhollow Ave

Pelham Brantmart
509-555-0187
4716 W Dunmore Ave

Copper Bluff Brantmart
509-555-0163
3854 S Kettering Rd

Facebook icon. www.clearbrookoptix.example

Nice open white space on back for writing next appointment time.

Target Market(s)

Main target is female 25-50, but I would like broad appeal.

Industry/Entity Type

Healthcare

Contact Information for Business Card

Modern look

Font styles to use
Serif

Requirements
Must have
• Logo and Dr Tavin R Marquell and Associates on front.
• 3 locations on back
• white space for noting next appointment

```html
<!DOCTYPE html>
<html lang="en">
<head>
<meta charset="utf-8">
<title>Clearbrook Optics – Business Card</title>
<link rel="stylesheet" href="https://fonts.googleapis.com/css2?family=Exo+2:wght@400;600;700&display=swap">
<style>
  :root {
    --page-bg: #5b5b5d;
    --card-white: #ffffff;
    --navy: #1d2f6a;
    --label-blue: #1f3d7a;
    --blue-light: #0b8fd8;
    --blue-dark: #1b3c7c;
    --swoosh-grey: #b1b3b6;
    --text-light: #e6f1fb;
    --line: #3a4f80;
  }
  * { margin: 0; padding: 0; box-sizing: border-box; }
  html, body {
    width: 1105px; height: 1200px; overflow: hidden;
    background: var(--page-bg);
    font-family: "Exo 2", sans-serif;
  }
  .card {
    position: absolute;
    left: 192px;
    width: 720px; height: 413px;
    border-radius: 22px;
    overflow: hidden;
    background: var(--card-white);
  }
  .card--front { top: 160px; }
  .card--back { top: 617px; }
  .card__bg { position: absolute; inset: 0; width: 100%; height: 100%; }

  .social-mark {
    position: absolute; left: 665px; top: 22px;
    width: 30px; height: 30px;
    background: var(--blue-light);
  }
  .brand {
    position: absolute; left: 0; right: 0; top: 140px;
    text-align: center;
  }
  .brand__name {
    font-size: 40px; font-weight: 600; color: var(--navy);
    letter-spacing: 1px; text-transform: uppercase; line-height: 1;
  }
  .brand__tagline {
    margin-top: 8px;
    font-size: 19px; font-weight: 700; color: var(--navy);
    letter-spacing: 0.5px; text-transform: uppercase;
  }
  .practice-name {
    position: absolute; left: 0; right: 0; top: 335px;
    text-align: center;
    font-size: 24px; font-weight: 600; color: #fff;
  }

  .locations {
    position: absolute; left: 0; right: 0; top: 33px;
    list-style: none; text-align: center;
    font-size: 19px; line-height: 29px; color: var(--text-light);
  }
  .locations__store { font-weight: 700; color: #fff; }

  .appointment { position: absolute; inset: 0; }
  .appointment__row {
    position: absolute; display: flex; align-items: flex-end;
    font-size: 19px; font-weight: 700; color: var(--label-blue);
  }
  .appointment__blank {
    display: inline-block; border-bottom: 1.5px solid var(--line);
    height: 20px; margin-left: 6px;
  }
  .appointment__row--name { left: 174px; top: 257px; }
  .appointment__row--name .appointment__blank { width: 340px; margin-left: 2px; }
  .appointment__row--date { left: 220px; top: 301px; }
  .appointment__row--date .appointment__blank { width: 255px; margin-left: 16px; }
  .appointment__row--time { left: 240px; top: 344px; }
  .appointment__row--time .appointment__blank { width: 139px; margin-left: 16px; margin-right: 12px; }
</style>
</head>
<body>

<section class="card card--front" aria-label="Card front">
  <svg class="card__bg" viewBox="0 0 720 413" preserveAspectRatio="none" aria-hidden="true">
    <defs>
      <radialGradient id="frontBlue" cx="360" cy="340" r="420" gradientUnits="userSpaceOnUse">
        <stop offset="0" stop-color="#0b8fd8"/>
        <stop offset="1" stop-color="#1b3c7c"/>
      </radialGradient>
    </defs>
    <path d="M0,160 Q360,360 720,160 L720,413 L0,413 Z" fill="#b1b3b6"/>
    <path d="M0,170 Q360,370 720,170 L720,413 L0,413 Z" fill="url(#frontBlue)"/>
  </svg>
  <span class="social-mark" aria-hidden="true"></span>
  <div class="brand">
    <div class="brand__name">Clearbrook Optics</div>
    <div class="brand__tagline">Advanced Eye Care</div>
  </div>
  <p class="practice-name">Dr Tavin R Marquell &amp; Associates</p>
</section>

<section class="card card--back" aria-label="Card back">
  <svg class="card__bg" viewBox="0 0 720 413" preserveAspectRatio="none" aria-hidden="true">
    <defs>
      <radialGradient id="backBlue" cx="360" cy="80" r="420" gradientUnits="userSpaceOnUse">
        <stop offset="0" stop-color="#0b8fd8"/>
        <stop offset="1" stop-color="#1b3c7c"/>
      </radialGradient>
    </defs>
    <path d="M0,0 L720,0 L720,278 Q360,52 0,278 Z" fill="#b1b3b6"/>
    <path d="M0,0 L720,0 L720,268 Q360,42 0,268 Z" fill="url(#backBlue)"/>
  </svg>
  <ul class="locations">
    <li><span class="locations__store">Pelham Brantmart</span> - 509-555-0187, 4716 W Dunmore Ave</li>
    <li><span class="locations__store">Copper Bluff Brantmart</span> - 509-555-0163, 3854 S Kettering Rd</li>
    <li><span class="locations__store">Ridgefront Brantmart</span> - 509-555-0142, 18342 E Fernhollow Ave</li>
  </ul>
  <div class="appointment">
    <div class="appointment__row appointment__row--name">Name<span class="appointment__blank"></span></div>
    <div class="appointment__row appointment__row--date">Date<span class="appointment__blank"></span></div>
    <div class="appointment__row appointment__row--time">Time<span class="appointment__blank"></span>am/pm</div>
  </div>
</section>

</body>
</html>
```